Business Card for Professional Photographer

I'm looking for an eye catching modern clean design that compliments my logo/ website fonts & colours.
I specialise in architecture, corporate & commercial photography so I'm marketing to professional clients rather than portrait / wedding clients.

I would prefer to not have a solid black design.

My logo brand guide is as follows :

Main front font. : Reislust
Main font colour : #fff
Slogan front font : Ubuntu Bold
Monogram front font : Venti Medium
Container colour : #fff

I need print ready files in pdf .png & .eps formats.

Included in the files below are some screen grabs as reference to font & colours etc.

```html
<!DOCTYPE html>
<html lang="en">
<head>
<meta charset="utf-8">
<title>Halewood Studio – Business Card</title>
<link rel="stylesheet" href="https://fonts.googleapis.com/css2?family=Roboto:wght@400;500&family=Khand:wght@600&display=swap">
<style>
  :root {
    --backdrop: #b4b4b4;
    --gold-light: #e6dc9c;
    --gold-mid: #cfb370;
    --gold-deep: #b38f4c;
    --gold-ink: #b08a44;
    --ink: #1b1b1b;
    --text: #3a3a3a;
    --paper: #f4f4f4;
    --paper-edge: #e6e6e6;
  }
  * { margin: 0; padding: 0; box-sizing: border-box; }
  html, body { width: 1200px; height: 576px; overflow: hidden; }
  body { background: var(--backdrop); position: relative; font-family: "Roboto", sans-serif; }

  .card {
    position: absolute;
    top: 139px;
    border-radius: 10px;
    box-shadow: 2px 3px 6px rgba(0,0,0,0.25);
    overflow: hidden;
  }

  /* Front */
  .card--front {
    left: 82px; width: 485px; height: 293px;
    background: linear-gradient(120deg, var(--gold-deep) 0%, var(--gold-mid) 45%, var(--gold-light) 100%);
  }
  .front__brand { position: absolute; left: 70px; top: 112px; display: flex; align-items: center; gap: 22px; }
  .brand-square { width: 52px; height: 52px; background: var(--ink); flex: none; }
  .brand-name {
    font-family: "Roboto", sans-serif; font-weight: 400;
    font-size: 30px; letter-spacing: 0.5px; color: var(--ink); line-height: 1;
  }
  .brand-tagline {
    font-family: "Roboto", sans-serif; font-weight: 500;
    font-size: 10px; letter-spacing: 1px; color: var(--ink); margin-top: 7px;
  }
  .front__url {
    position: absolute; left: 0; right: 0; top: 256px; text-align: center;
    font-family: "Roboto", sans-serif; font-weight: 400;
    font-size: 13px; letter-spacing: 1.5px; color: var(--ink);
  }

  /* Back */
  .card--back {
    left: 602px; width: 481px; height: 290px;
    background: linear-gradient(160deg, #fafafa 0%, var(--paper) 60%, var(--paper-edge) 100%);
  }
  .back__name {
    position: absolute; left: 30px; top: 34px;
    font-family: "Khand", sans-serif; font-weight: 600; font-size: 21px;
    color: var(--gold-ink); line-height: 1;
  }
  .back__role { position: absolute; left: 30px; top: 60px; font-size: 13px; color: var(--text); }
  .contact { position: absolute; left: 30px; top: 183px; list-style: none; }
  .contact li { display: flex; align-items: center; height: 18.5px; font-size: 12.5px; color: var(--text); }
  .contact svg { width: 11px; height: 11px; margin-left: 6px; margin-right: 13px; fill: var(--gold-ink); }
  .back__address { position: absolute; left: 30px; top: 242px; font-size: 12.5px; color: var(--text); }

  .back__brand { position: absolute; left: 286px; top: 166px; width: 170px; text-align: center; }
  .back__brand .brand-square { width: 42px; height: 42px; background: var(--gold-ink); margin: 0 auto 16px; }
  .back__brand .brand-name { font-size: 21px; color: var(--text); }
  .back__brand .brand-tagline { font-size: 8px; color: var(--text); margin-top: 5px; }
</style>
</head>
<body>

<section class="card card--front">
  <div class="front__brand">
    <div class="brand-square"></div>
    <div>
      <div class="brand-name">Halewood Studio</div>
      <div class="brand-tagline">Buildings · Business · Brands</div>
    </div>
  </div>
  <div class="front__url">www.halewoodstudio.com.au</div>
</section>

<section class="card card--back">
  <div class="back__name">Aaron Hale</div>
  <div class="back__role">Photographer</div>

  <ul class="contact">
    <li>
      <svg viewBox="0 0 12 12"><path d="M1 3.5C1 2 2.5 1 6 1s5 1 5 2.5V5H8.5V4h-5v1H1zM2.5 6h7l1 5h-9z"/></svg>
      0412586730
    </li>
    <li>
      <svg viewBox="0 0 12 12"><path d="M1 2.5h10v7H1zM1.5 3l4.5 3.5L10.5 3v1L6 7.5 1.5 4z" fill-rule="evenodd"/></svg>
      info@halewoodstudio.com.au
    </li>
    <li>
      <svg viewBox="0 0 12 12"><circle cx="6" cy="6" r="5"/><path d="M1 6h10M6 1v10" stroke="#f4f4f4" stroke-width="0.8"/></svg>
      www.halewoodstudio.com.au
    </li>
  </ul>
  <div class="back__address">24 Mill Lane Oakridge Vic 3280</div>

  <div class="back__brand">
    <div class="brand-square"></div>
    <div class="brand-name">Halewood Studio</div>
    <div class="brand-tagline">Buildings · Business · Brands</div>
  </div>
</section>

</body>
</html>
```